Elevating our current Business Card Design

We want to elevate our current business card with a new design to look like a zenith 300 company. We are a premium lubricant distributor (oil and grease).
We need 2 versions, version 1 is as per the uploaded a copy of our current business card with the English version.
For our Chinese version we need to use the front to be English in English and have the back of the card designed exactly like the front for all info to be in Chinese.
The design template needs to be such that we can amend the template with adding different information for each person's card.
The background colour of the card can be changed- we just need to clearly see all information on the card and logos.
The QJR and Ember steady logos cannot have any colour or display changes- only use the logos attached.
All logos need to be included and all information from the attached current card

```html
<!DOCTYPE html>
<html lang="en">
<head>
<meta charset="utf-8">
<title>Harbrook Business Card – Front and Back</title>
<link rel="stylesheet" href="https://fonts.googleapis.com/css2?family=Open+Sans:wght@400;600;700&family=Varela+Round&display=swap">
<style>
  :root {
    --backdrop: #dcdde0;
    --card: #ffffff;
    --red: #e52b24;
    --red-dark: #a8181d;
    --gold: #e9b12e;
    --ink: #1d1d1d;
    --grey: #8a8b8f;
    --badge-orange: #ef7d22;
    --badge-green: #1e4d2b;
  }
  * { box-sizing: border-box; margin: 0; padding: 0; }
  html, body { width: 1200px; height: 780px; overflow: hidden; }
  body {
    background: var(--backdrop);
    font-family: "Open Sans", sans-serif;
    color: var(--ink);
    position: relative;
  }
  .card {
    position: absolute;
    top: 236px;
    width: 540px;
    height: 308px;
    background: var(--card);
    overflow: hidden;
    box-shadow: 0 10px 24px rgba(0,0,0,0.18);
  }
  .card--front { left: 40px; }
  .card--back { left: 620px; }

  /* Front */
  .corner-tab {
    position: absolute; top: 0; right: 0;
    width: 34px; height: 52px; background: var(--red);
  }
  .identity {
    position: absolute; top: 30px; right: 52px; text-align: right;
  }
  .identity__name {
    font-family: "Varela Round", sans-serif;
    font-size: 30px; font-weight: 400; color: var(--red); line-height: 1.1;
  }
  .identity__title { font-size: 14px; letter-spacing: 0.2px; margin-top: 2px; }
  .divider {
    position: absolute; top: 104px; left: 40px; right: 52px;
    height: 1px; background: var(--ink);
  }
  .brand-word {
    position: absolute; top: 44px; left: 40px;
    font-size: 36px; font-weight: 700; color: var(--red); line-height: 1;
  }
  .contacts {
    position: absolute; left: 40px; top: 130px; list-style: none;
    font-size: 15px; line-height: 27px;
  }
  .contacts li { display: flex; align-items: center; gap: 10px; }
  .contacts svg { width: 15px; height: 15px; flex: none; }
  .address {
    position: absolute; top: 122px; right: 52px; text-align: right;
    font-size: 15px; line-height: 22px;
  }
  .swoosh { position: absolute; right: 0; bottom: 0; width: 540px; height: 308px; }

  /* Back */
  .hero-word {
    position: absolute; top: 70px; left: 0; right: 0; text-align: center;
    font-size: 84px; font-weight: 700; color: var(--red); line-height: 1;
  }
  .accreditations {
    position: absolute; left: 24px; right: 24px; bottom: 26px;
    display: flex; align-items: center; justify-content: space-between;
  }
  .badge { width: 42px; height: 42px; border-radius: 50%; }
  .badge--climate { background: var(--badge-green); border-radius: 50% 50% 8px 8px; width: 50px; height: 38px; }
  .badge--cert { background: var(--badge-orange); border: 4px solid var(--grey); }
  .partner {
    border: 2px solid var(--red); padding: 6px 10px;
    font-size: 11px; font-weight: 600; color: var(--red); line-height: 1.2;
    max-width: 150px;
  }
  .partner-name { font-size: 16px; font-weight: 700; color: var(--red); }
</style>
</head>
<body>

<section class="card card--front" aria-label="Business card front">
  <div class="corner-tab"></div>

  <div class="brand-word">Harbrook</div>

  <div class="identity">
    <h1 class="identity__name">Mara Kellow</h1>
    <p class="identity__title">Administration Executive</p>
  </div>
  <div class="divider"></div>

  <ul class="contacts">
    <li><svg viewBox="0 0 16 16"><path d="M3 2l3 1 1 3-2 1a8 8 0 0 0 4 4l1-2 3 1 1 3-2 1C7 14 2 9 2 4z" fill="#e52b24"/></svg>1300 000 481</li>
    <li><svg viewBox="0 0 16 16"><rect x="4" y="1" width="8" height="14" rx="1.5" fill="none" stroke="#e52b24" stroke-width="1.6"/></svg>+61 400 000 217</li>
    <li><svg viewBox="0 0 16 16"><rect x="2" y="6" width="12" height="8" rx="1" fill="#e52b24"/><rect x="4" y="2" width="8" height="5" fill="none" stroke="#e52b24" stroke-width="1.4"/></svg>+61 8 9000 4410</li>
    <li><svg viewBox="0 0 16 16"><circle cx="8" cy="8" r="6.5" fill="none" stroke="#e52b24" stroke-width="1.6"/><path d="M1.5 8h13M8 1.5c-3 3-3 10 0 13M8 1.5c3 3 3 10 0 13" fill="none" stroke="#e52b24" stroke-width="1.2"/></svg>www.harbrookdirect.example</li>
    <li><svg viewBox="0 0 16 16"><rect x="1.5" y="3.5" width="13" height="9" fill="none" stroke="#e52b24" stroke-width="1.6"/><path d="M1.5 3.5l6.5 5 6.5-5" fill="none" stroke="#e52b24" stroke-width="1.4"/></svg>mara.kellow@harbrookdirect.example</li>
  </ul>

  <p class="address">48 Harbour Freight Way<br>Westmere, WA 6999</p>

  <svg class="swoosh" viewBox="0 0 540 308" aria-hidden="true">
    <path d="M540 150 C500 250 440 290 330 308 L540 308 Z" fill="var(--gold)"/>
    <path d="M540 150 C505 240 450 285 330 308 L300 308 C430 290 500 240 540 120 Z" fill="var(--red)"/>
    <path d="M540 120 C500 240 430 290 300 308 L280 308 C420 292 495 235 540 100 Z" fill="var(--red-dark)"/>
  </svg>
</section>

<section class="card card--back" aria-label="Business card back">
  <div class="hero-word">Harbrook</div>

  <div class="accreditations">
    <div class="badge badge--climate" role="img" aria-label="Ember steady network member badge"></div>
    <div class="badge badge--cert" role="img" aria-label="QJR certification badge"></div>
    <div class="partner">Harbrook Lubricant Distributors</div>
    <span class="partner-name">Norvane</span>
    <div class="badge badge--cert" role="img" aria-label="QJR certification badge"></div>
    <div class="badge badge--cert" role="img" aria-label="QJR certification badge"></div>
  </div>
</section>

</body>
</html>
```